KRT Project Signage

Need a sign to be displayed in the front of properties currently under Construction or Renovation to advertise our company information. Need it to be Professional and Contemporary. We are a Design/Build Construction Company. Information should include Company Name, email, website, phone number. Attached: Logo and company brochure, also included and inspiration images

```html
<!DOCTYPE html>
<html lang="en">
<head>
<meta charset="utf-8">
<title>KRT Project Signage</title>
<link rel="stylesheet" href="https://fonts.googleapis.com/css2?family=Poppins:wght@500;600;700&display=swap">
<style>
  :root {
    --page: #ffffff;
    --sign-white: #ffffff;
    --ink: #111111;
    --band-black: #0b0b0b;
    --panel-grey: #4f4f4f;
    --panel-grey-deep: #3f3f3f;
    --accent-yellow: #f1ee45;
    --text-light: #ffffff;
  }
  * { box-sizing: border-box; margin: 0; padding: 0; }
  html, body {
    width: 1200px;
    height: 3455px;
    overflow: hidden;
    background: var(--page);
    font-family: "Poppins", Arial, sans-serif;
  }
  .sign {
    position: absolute;
    left: 80px;
    top: 948px;
    width: 1040px;
    height: 1560px;
    background: var(--sign-white);
    box-shadow: 0 18px 50px rgba(0,0,0,0.28);
  }
  .brand {
    position: absolute;
    left: 0; right: 0;
    top: 130px;
    text-align: center;
    color: var(--ink);
  }
  .brand-name {
    display: inline-flex;
    align-items: center;
    gap: 22px;
    font-size: 66px;
    font-weight: 600;
    letter-spacing: 2px;
    line-height: 1;
  }
  .brand-dot {
    width: 40px; height: 40px;
    border-radius: 50%;
    background: var(--accent-yellow);
  }
  .brand-tagline {
    margin-top: 26px;
    font-size: 38px;
    font-weight: 500;
    letter-spacing: 3px;
    line-height: 1;
  }
  .brand-web {
    margin-top: 22px;
    font-size: 30px;
    font-weight: 600;
    line-height: 1;
  }
  .info-panel {
    position: absolute;
    left: 0; right: 0;
    top: 540px;
    height: 852px;
    background: linear-gradient(180deg, var(--panel-grey) 0%, var(--panel-grey-deep) 100%);
  }
  .phone-pill {
    position: absolute;
    left: 75px;
    top: 484px;
    width: 882px;
    height: 148px;
    border-radius: 74px;
    background: var(--band-black);
    border: 4px solid var(--sign-white);
    display: flex;
    align-items: center;
    justify-content: center;
    gap: 34px;
    color: var(--text-light);
    font-size: 106px;
    font-weight: 700;
    line-height: 1;
  }
  .phone-pill svg { width: 72px; height: 72px; }
  .contact {
    position: absolute;
    left: 0; right: 0;
    text-align: center;
    color: var(--text-light);
  }
  .contact svg { display: block; margin: 0 auto; }
  .fax { top: 676px; }
  .fax-number { margin-top: 14px; font-size: 74px; font-weight: 700; line-height: 1; }
  .email { top: 890px; }
  .email-address { margin-top: 14px; font-size: 50px; font-weight: 500; line-height: 1; }
  .address { top: 1080px; }
  .address-lines { margin-top: 14px; font-size: 46px; font-weight: 500; line-height: 59px; }
  .footer-band {
    position: absolute;
    left: 0; right: 0; bottom: 0;
    height: 168px;
    background: var(--band-black);
    color: var(--text-light);
    display: flex;
    align-items: center;
    justify-content: center;
    font-size: 60px;
    font-weight: 700;
  }
</style>
</head>
<body>
  <main class="sign">
    <header class="brand">
      <div class="brand-name"><span>KRT CONSTRUCTION</span><span class="brand-dot"></span></div>
      <div class="brand-tagline">LUXURY RENOVATIONS</div>
      <div class="brand-web">www.krtconstruction.com</div>
    </header>

    <section class="info-panel" role="img" aria-label="Muted photo of a finished luxury interior behind the contact details"></section>

    <div class="phone-pill">
      <svg viewBox="0 0 64 64" aria-hidden="true">
        <path fill="var(--accent-yellow)" d="M14 6c3-2 6-1 8 2l6 9c1.5 2.5 1 5-1 7l-4 3c3 7 8 12 15 15l3-4c2-2 4.5-2.5 7-1l9 6c3 2 4 5 2 8l-4 5c-2 3-6 4-10 3C27 54 10 37 5 19c-1-4 0-8 3-10z"/>
        <path fill="none" stroke="var(--accent-yellow)" stroke-width="4" stroke-linecap="round" d="M38 10a18 18 0 0 1 16 16M37 20a8 8 0 0 1 7 7"/>
      </svg>
      <span>555.014.2207</span>
    </div>

    <div class="contact fax">
      <svg width="62" height="62" viewBox="0 0 64 64" aria-hidden="true">
        <rect x="4" y="22" width="14" height="38" rx="3" fill="var(--text-light)"/>
        <rect x="22" y="22" width="38" height="38" rx="3" fill="var(--text-light)"/>
        <rect x="28" y="4" width="26" height="18" fill="var(--text-light)"/>
        <g fill="var(--panel-grey)">
          <rect x="28" y="30" width="26" height="7"/>
          <rect x="28" y="42" width="6" height="5"/><rect x="38" y="42" width="6" height="5"/><rect x="48" y="42" width="6" height="5"/>
          <rect x="28" y="51" width="6" height="5"/><rect x="38" y="51" width="6" height="5"/><rect x="48" y="51" width="6" height="5"/>
        </g>
      </svg>
      <div class="fax-number">555.014.2290</div>
    </div>

    <div class="contact email">
      <svg width="62" height="58" viewBox="0 0 64 60" aria-hidden="true">
        <path fill="var(--text-light)" d="M2 24 32 2l30 22v34H2z"/>
        <rect x="14" y="10" width="36" height="28" fill="var(--panel-grey)"/>
        <circle cx="32" cy="22" r="7" fill="none" stroke="var(--text-light)" stroke-width="3"/>
        <path fill="none" stroke="var(--panel-grey)" stroke-width="3" d="M2 24l30 20 30-20M2 58l24-18M62 58 38 40"/>
      </svg>
      <div class="email-address">info@krtconstruction.com</div>
    </div>

    <div class="contact address">
      <svg width="62" height="66" viewBox="0 0 64 68" aria-hidden="true">
        <ellipse cx="32" cy="56" rx="26" ry="9" fill="none" stroke="var(--text-light)" stroke-width="4"/>
        <path fill="var(--text-light)" d="M32 2c11 0 19 8 19 19 0 13-19 37-19 37S13 34 13 21C13 10 21 2 32 2z"/>
        <circle cx="32" cy="21" r="7" fill="var(--panel-grey)"/>
      </svg>
      <div class="address-lines">1480 Harbor View Rd.<br>Suite 310<br>Lakeside, FL 33499</div>
    </div>

    <footer class="footer-band">www.krtconstruction.com</footer>
  </main>
</body>
</html>
```